Law Offices business card

Hi there, I'll need business card for the Law Offices of Colin Matheny. The information must convey his strategic approach and quick resolution to complex business litigation needs. Please emphasize Civil Litigation, Corporate Law, Business Governance and Real Estate Law. Colin has over 25 years of experience in these fields.The card should be modern and edgy and the message should be clear. Please consult his current website for ideas.

```html
<!DOCTYPE html>
<html lang="en">
<head>
<meta charset="utf-8">
<title>Law Offices of Colin Matheny – Business Card</title>
<link rel="stylesheet" href="https://fonts.googleapis.com/css2?family=Arimo:wght@400;700&display=swap">
<style>
  :root {
    --brand-red: #c0504e;
    --ink-black: #0b0b0b;
    --paper-white: #ffffff;
    --backdrop: #e6e6e6;
  }
  html, body {
    margin: 0;
    width: 1200px;
    height: 950px;
    overflow: hidden;
    background: var(--backdrop);
    font-family: "Arimo", Arial, sans-serif;
  }
  .sheet {
    position: relative;
    width: 1200px;
    height: 950px;
  }
  .card {
    position: absolute;
    left: 250px;
    width: 700px;
    height: 400px;
    overflow: hidden;
    box-shadow: 0 10px 28px rgba(0,0,0,.22);
  }
  .card--back { top: 50px; background: var(--brand-red); }
  .card--front { top: 500px; background: var(--brand-red); }

  /* back side */
  .back-name {
    position: absolute;
    top: 150px;
    left: 0;
    width: 100%;
    text-align: center;
    color: var(--paper-white);
    font-weight: 700;
    font-size: 30px;
    letter-spacing: 1px;
  }
  .back-name .mark-square {
    display: inline-block;
    width: 14px;
    height: 14px;
    background: var(--paper-white);
    margin-right: 12px;
    vertical-align: 3px;
  }
  .back-web {
    position: absolute;
    top: 262px;
    left: 0;
    width: 100%;
    display: flex;
    justify-content: center;
    align-items: center;
    gap: 16px;
    color: var(--paper-white);
    font-size: 16px;
    letter-spacing: 5px;
  }
  .back-web .rule {
    width: 70px;
    height: 2px;
    background: var(--paper-white);
  }

  /* front side */
  .front-shape { position: absolute; inset: 0; }
  .firm {
    position: absolute;
    left: 50px;
    top: 118px;
    color: var(--paper-white);
    font-weight: 700;
  }
  .firm-prefix {
    font-size: 14px;
    letter-spacing: 2px;
    text-transform: uppercase;
    display: flex;
    align-items: center;
    gap: 10px;
  }
  .firm-prefix .mark-square {
    width: 12px;
    height: 12px;
    background: var(--brand-red);
  }
  .firm-name {
    font-size: 36px;
    line-height: 1.05;
    margin-top: 6px;
  }
  .contact {
    position: absolute;
    right: 30px;
    top: 44px;
    text-align: right;
    color: var(--paper-white);
  }
  .contact-name { font-size: 20px; font-weight: 700; }
  .contact-title { font-size: 14px; margin-top: 2px; margin-bottom: 12px; }
  .contact-list { list-style: none; margin: 0; padding: 0; }
  .contact-list li {
    display: flex;
    justify-content: flex-end;
    align-items: center;
    gap: 10px;
    font-size: 15px;
    line-height: 24px;
  }
  .contact-list .icon { width: 16px; height: 16px; flex: none; }
  .contact-list .icon--blank { visibility: hidden; }
</style>
</head>
<body>
<main class="sheet">

  <section class="card card--back" aria-label="Card back">
    <div class="back-name"><span class="mark-square"></span>Colin Matheny</div>
    <div class="back-web"><span class="rule"></span>www.example.com<span class="rule"></span></div>
  </section>

  <section class="card card--front" aria-label="Card front">
    <svg class="front-shape" viewBox="0 0 700 400" width="700" height="400" aria-hidden="true">
      <path d="M0 0 H420 C372 24 368 140 338 212 C300 300 200 322 0 300 Z" fill="var(--ink-black)"/>
      <path d="M420 0 H446 C400 24 396 150 366 228 C326 322 200 350 0 328 V300 C200 322 300 300 338 212 C368 140 372 24 420 0 Z" fill="var(--paper-white)"/>
      <path d="M446 0 C400 24 396 150 366 228 C326 322 200 350 0 328" fill="none" stroke="var(--ink-black)" stroke-width="2"/>
    </svg>

    <div class="firm">
      <div class="firm-prefix"><span class="mark-square"></span>Law Offices of</div>
      <div class="firm-name">Colin<br>Matheny, PA</div>
    </div>

    <div class="contact">
      <div class="contact-name">Colin Matheny</div>
      <div class="contact-title">President</div>
      <ul class="contact-list">
        <li>4127 Harbor Lane<svg class="icon icon--blank" viewBox="0 0 16 16"></svg></li>
        <li>Maple Grove, NY 10990
          <svg class="icon" viewBox="0 0 16 16" fill="#fff"><path d="M3 2h3l1 4-2 1a8 8 0 0 0 4 4l1-2 4 1v3a1 1 0 0 1-1 1A12 12 0 0 1 2 3a1 1 0 0 1 1-1z"/></svg></li>
        <li>555 0142 7781
          <svg class="icon" viewBox="0 0 16 16" fill="none" stroke="#fff" stroke-width="1.6"><rect x="4" y="1" width="8" height="14" rx="1.5"/><line x1="7" y1="12.5" x2="9" y2="12.5"/></svg></li>
        <li>555 0198 3320
          <svg class="icon" viewBox="0 0 16 16" fill="#fff"><rect x="1" y="6" width="14" height="8" rx="1"/><rect x="4" y="2" width="8" height="4"/></svg></li>
        <li>555 0167 4409
          <svg class="icon" viewBox="0 0 16 16" fill="#fff"><rect x="1" y="6" width="14" height="8" rx="1"/><rect x="4" y="2" width="8" height="4"/></svg></li>
        <li>colin@example.com
          <svg class="icon" viewBox="0 0 16 16" fill="none" stroke="#fff" stroke-width="1.6"><rect x="1" y="3" width="14" height="10" rx="1"/><path d="M1 4l7 5 7-5"/></svg></li>
        <li>www.example.com
          <svg class="icon" viewBox="0 0 16 16" fill="none" stroke="#fff" stroke-width="1.4"><circle cx="8" cy="8" r="6.5"/><ellipse cx="8" cy="8" rx="3" ry="6.5"/><line x1="1.5" y1="8" x2="14.5" y2="8"/></svg></li>
      </ul>
    </div>
  </section>

</main>
</body>
</html>
```